Business Card Design Project

I require a business card with the following information on them for various different people;
name
m:
f:
e:
I have a logo already and will attached that. We are in the construction industry. I require something clean and simple but eye catching at the same time. You can use another colour with our logo if you like and you can style the logo as well if you wish. I am open.
Also it needs to be front and back design.
Industry/Entity Type
Construction
Requirements
Must have
- Logo, name, mobile, fax and email address.
Front and back design

```html
<!DOCTYPE html>
<html lang="en">
<head>
<meta charset="utf-8">
<title>Stoneline Builders – Business Cards</title>
<link rel="stylesheet" href="https://fonts.googleapis.com/css2?family=Arimo:wght@400;700&display=swap">
<style>
  :root {
    --backdrop: #262626;
    --card-black: #050505;
    --card-charcoal: #1e1e1e;
    --brand-green: #8cc63f;
    --deco-green: #7ab831;
    --deco-silver: #a9a9a9;
    --deco-grey: #3a3a3a;
    --text-white: #ffffff;
    --text-grey: #cfcfcf;
    --rule-grey: #4a4a4a;
  }
  * { box-sizing: border-box; margin: 0; padding: 0; }
  html, body {
    width: 1200px;
    height: 900px;
    overflow: hidden;
    background: var(--backdrop);
    font-family: "Arimo", Arial, sans-serif;
  }
  .sheet {
    position: relative;
    width: 1200px;
    height: 900px;
  }
  .card {
    position: absolute;
    left: 250px;
    width: 700px;
    height: 395px;
    border-radius: 30px;
    overflow: hidden;
    background: radial-gradient(ellipse at 55% 20%, var(--card-charcoal) 0%, var(--card-black) 70%);
    box-shadow: 0 14px 30px rgba(0,0,0,0.55);
  }
  .card--front { top: 35px; }
  .card--back { top: 465px; }

  .decoration {
    position: absolute;
  }
  .decoration--front-side {
    left: 0;
    top: 0;
    width: 240px;
    height: 100%;
    background: linear-gradient(90deg, var(--deco-green) 0%, var(--deco-green) 55%, var(--deco-grey) 100%);
  }
  .decoration--back-stripe {
    left: 0;
    top: 262px;
    width: 100%;
    height: 66px;
    background: linear-gradient(180deg, var(--deco-grey) 0%, var(--deco-silver) 100%);
  }

  .brand-name {
    position: absolute;
    font-family: "Arimo", Arial, sans-serif;
    font-weight: 400;
    color: var(--brand-green);
    letter-spacing: 1px;
    white-space: nowrap;
    display: flex;
    align-items: center;
    justify-content: center;
    gap: 12px;
  }
  .brand-name__square {
    display: inline-block;
    background: var(--brand-green);
  }
  .card--front .brand-name {
    left: 270px;
    right: 20px;
    top: 78px;
    font-size: 34px;
  }
  .card--front .brand-name__square { width: 20px; height: 20px; }
  .card--back .brand-name {
    left: 0;
    right: 0;
    top: 120px;
    font-size: 46px;
  }
  .card--back .brand-name__square { width: 28px; height: 28px; }

  .identity {
    position: absolute;
    left: 280px;
    top: 180px;
    display: flex;
    align-items: baseline;
    gap: 12px;
    white-space: nowrap;
  }
  .identity__name {
    color: var(--brand-green);
    font-size: 24px;
    letter-spacing: 0.5px;
  }
  .identity__title {
    color: var(--text-grey);
    font-size: 17px;
    border-left: 2px solid var(--text-grey);
    padding-left: 10px;
    line-height: 16px;
  }
  .identity-rule {
    position: absolute;
    left: 270px;
    top: 220px;
    width: 400px;
    height: 1px;
    background: var(--rule-grey);
  }
  .contact {
    position: absolute;
    left: 280px;
    top: 236px;
    width: 395px;
    display: grid;
    grid-template-columns: auto auto;
    justify-content: space-between;
    row-gap: 8px;
    column-gap: 10px;
    font-size: 12.5px;
    color: var(--text-white);
    white-space: nowrap;
  }
  .contact__label { color: var(--brand-green); }
  .contact__item--right { text-align: right; }
</style>
</head>
<body>
<main class="sheet">

  <section class="card card--front" aria-label="Business card front">
    <div class="decoration decoration--front-side" role="img" aria-label="Green and silver side decoration"></div>

    <div class="brand-name"><span class="brand-name__square"></span>Stoneline Builders</div>

    <div class="identity">
      <span class="identity__name">YOUR NAME</span>
      <span class="identity__title">Job Title</span>
    </div>
    <div class="identity-rule"></div>

    <div class="contact">
      <span class="contact__item">Street Name, City, State, Zip Code</span>
      <span class="contact__item contact__item--right"><span class="contact__label">Mobile :</span> xxxxxxxxxx</span>
      <span class="contact__item"><span class="contact__label">Fax :</span> xxx xxx xxxx</span>
      <span class="contact__item contact__item--right"><span class="contact__label">E-mail :</span> name@Website.com</span>
    </div>
  </section>

  <section class="card card--back" aria-label="Business card back">
    <div class="brand-name"><span class="brand-name__square"></span>Stoneline Builders</div>
    <div class="decoration decoration--back-stripe" role="img" aria-label="Green and silver stripe decoration"></div>
  </section>

</main>
</body>
</html>
```